Business Card Design (NEW FILES)

ATTENTION: New vector files are available. Please update your design to reflect/use the new (better resolution) logo images.

Seeking a unique and professional business card design for a commercial drone photography/videography business. The layout should feature
the logo (attached) and include the following information:
Owen Tarrick
614-502-7738
www.skylarkreelworks.example
NRD Certified Remote Pilot

Owen Tarrick

```html
<!DOCTYPE html>
<html lang="en">
<head>
<meta charset="utf-8">
<title>Skylark Reelworks — Business Card</title>
<link href="https://fonts.googleapis.com/css2?family=Open+Sans:wght@400;600;700&display=swap" rel="stylesheet">
<style>
  :root {
    --backdrop: #222222;
    --navy: #1b1c4b;
    --orange: #e6874d;
    --orange-deep: #d9763c;
    --paper: #ffffff;
    --shadow: rgba(0, 0, 0, 0.45);
  }
  * { box-sizing: border-box; margin: 0; padding: 0; }
  html, body {
    width: 1200px;
    height: 780px;
    overflow: hidden;
    background: var(--backdrop);
    font-family: "Open Sans", Arial, sans-serif;
  }
  .canvas {
    position: relative;
    width: 1200px;
    height: 780px;
  }
  .card {
    position: absolute;
    top: 240px;
    width: 525px;
    height: 300px;
    border-radius: 22px;
    overflow: hidden;
    box-shadow: 0 18px 40px var(--shadow);
  }
  .card-front { left: 50px; background: var(--paper); }
  .card-back { left: 625px; background: var(--orange); }

  .wave-art {
    position: absolute;
    inset: 0;
    width: 100%;
    height: 100%;
  }
  .wave-navy { fill: var(--navy); }
  .wave-orange { fill: var(--orange); }
  .wave-line { fill: var(--navy); }

  .brand {
    position: absolute;
    top: 30px;
    left: 32px;
    display: flex;
    align-items: center;
    gap: 10px;
  }
  .brand-dot {
    width: 16px;
    height: 16px;
    border-radius: 50%;
    background: var(--orange);
  }
  .brand-name {
    font-weight: 600;
    font-size: 22px;
    letter-spacing: 1px;
    color: var(--navy);
    text-transform: uppercase;
  }

  .contact {
    position: absolute;
    right: 36px;
    bottom: 20px;
    text-align: right;
    color: var(--paper);
  }
  .person-name {
    font-size: 25px;
    font-weight: 700;
    line-height: 1.1;
  }
  .person-name .first { color: var(--orange); }
  .person-role {
    font-size: 13px;
    margin-bottom: 8px;
  }
  .detail {
    font-size: 13px;
    line-height: 19px;
    display: flex;
    justify-content: flex-end;
    align-items: center;
    gap: 7px;
  }
  .detail-icon { width: 12px; height: 12px; fill: none; stroke: var(--orange); stroke-width: 1.6; }
  .detail-icon .solid { fill: var(--orange); stroke: none; }

  .back-mark {
    position: absolute;
    inset: 0;
    display: flex;
    align-items: center;
    justify-content: center;
    gap: 14px;
  }
  .back-dot {
    width: 26px;
    height: 26px;
    border-radius: 50%;
    background: var(--orange-deep);
  }
  .back-name {
    font-weight: 600;
    font-size: 30px;
    letter-spacing: 2px;
    text-transform: uppercase;
    color: var(--orange-deep);
  }
</style>
</head>
<body>
<main class="canvas">

  <section class="card card-front" aria-label="Business card front">
    <svg class="wave-art" viewBox="0 0 525 300" preserveAspectRatio="none" aria-hidden="true">
      <path class="wave-line" d="M0,78 C110,74 175,132 300,132 C390,132 470,110 525,118 L525,121 C470,114 390,137 300,137 C170,137 110,82 0,84 Z"/>
      <path class="wave-orange" d="M0,90 C110,86 170,146 300,143 C400,141 480,118 525,132 L525,140 C480,128 400,150 300,152 C170,156 110,98 0,98 Z"/>
      <path class="wave-navy" d="M0,105 C110,100 170,160 300,158 C400,156 480,135 525,150 L525,300 L0,300 Z"/>
    </svg>

    <div class="brand">
      <span class="brand-dot"></span>
      <span class="brand-name">Skylark Reelworks</span>
    </div>

    <div class="contact">
      <p class="person-name"><span class="first">Owen</span> Tarrick</p>
      <p class="person-role">Owner</p>
      <p class="detail">NRD Certified Remote Pilot</p>
      <p class="detail">Fully Insured</p>
      <p class="detail">614-502-7738
        <svg class="detail-icon" viewBox="0 0 12 12" aria-hidden="true"><path class="solid" d="M2.5,0.8 L4.4,3.2 L3.4,4.4 C4.1,5.9 5.9,7.7 7.6,8.6 L8.8,7.6 L11.2,9.5 L10.1,11.2 C5.6,11 1,6.4 0.8,1.9 Z"/></svg>
      </p>
      <p class="detail">www.skylarkreelworks.example
        <svg class="detail-icon" viewBox="0 0 12 12" aria-hidden="true"><circle cx="6" cy="6" r="5"/><path d="M1,6 H11 M6,1 C3.5,3.5 3.5,8.5 6,11 M6,1 C8.5,3.5 8.5,8.5 6,11"/></svg>
      </p>
    </div>
  </section>

  <section class="card card-back" aria-label="Business card back">
    <div class="back-mark">
      <span class="back-dot"></span>
      <span class="back-name">Skylark Reelworks</span>
    </div>
  </section>

</main>
</body>
</html>
```